A picture showing off our Million Dollar Renovation Update at Maple Ridge Splashpark Lodge

Use the uploaded images to develop a picture at least 1366x512 with text saying - Check out our Million Dollar Renovation - I have uploaded alot please use the best to show off . It will go as the hero picture on this website https://mapleridgesplash-example.com/ - would also to use in social in a "splash" manner to show off updates

Target Market(s)

visitors to our website and past guest

Industry/Entity Type

Hotel

Requirements
Must have
• Check out Our Million Dollar Renovation!
Nice to have
• pictures

```html
<!DOCTYPE html>
<html lang="en">
<head>
<meta charset="utf-8">
<title>Maple Ridge Splashpark Lodge – Million Dollar Renovation Banners</title>
<link rel="stylesheet" href="https://fonts.googleapis.com/css2?family=Graduate&display=swap">
<style>
  :root {
    --page-bg: #f3f3f3;
    --money-light: #e9e6cf;
    --money-mid: #d3d0b0;
    --money-dark: #a8a68a;
    --frame-line: #3e5a3a;
    --headline-dark: #2f3b2b;
    --headline-light: #f1ead3;
    --photo-warm: #9a6440;
    --photo-wall: #f2ede3;
    --photo-green: #9cc4a0;
    --photo-sky: #cfe9ec;
    --photo-dark: #5a4436;
    --tint-magenta: #d8336a;
    --tint-orange: #f0a040;
    --tint-yellow: #ece476;
    --tint-violet: #b05cc0;
  }
  * { margin: 0; padding: 0; box-sizing: border-box; }
  html, body { width: 1200px; height: 1200px; overflow: hidden; background: var(--page-bg); }
  .canvas { position: relative; width: 1200px; height: 1200px; }

  .banner {
    position: absolute; left: 96px; width: 1008px; height: 380px;
    box-shadow: 2px 3px 5px rgba(0,0,0,.35);
    overflow: hidden;
  }
  .banner--classic { top: 14px; }
  .banner--bright { top: 408px; }
  .banner--sunset { top: 803px; }

  .banner__money {
    position: absolute; inset: 0;
    background:
      radial-gradient(ellipse at 20% 30%, rgba(255,255,255,.35), transparent 60%),
      linear-gradient(115deg, var(--money-light) 0%, var(--money-mid) 45%, var(--money-light) 70%, var(--money-dark) 100%);
  }
  .banner__frame {
    position: absolute; left: 42px; top: 40px; width: 924px; height: 302px;
    border: 3px double var(--frame-line);
    padding: 4px;
  }
  .banner__photo {
    width: 100%; height: 100%;
    background:
      linear-gradient(180deg, rgba(255,255,255,.18) 0%, rgba(255,255,255,0) 45%, rgba(60,40,30,.15) 100%),
      linear-gradient(90deg,
        var(--photo-warm) 0%, var(--photo-wall) 38%,
        var(--photo-green) 62%, var(--photo-sky) 86%, var(--photo-dark) 100%);
  }
  .banner--bright .banner__photo { filter: brightness(1.06) saturate(0.9); }

  .banner--sunset .banner__money,
  .banner--sunset .banner__photo { filter: saturate(0.5); }
  .banner__tint {
    position: absolute; inset: 0; mix-blend-mode: multiply; opacity: .8;
    background: linear-gradient(100deg, var(--tint-magenta) 0%, var(--tint-orange) 40%, var(--tint-yellow) 62%, #f4e9c8 80%, var(--tint-violet) 100%);
  }

  .banner__headline {
    position: absolute; left: 0; right: 0; top: 118px;
    font-family: "Graduate", "Arial Black", sans-serif;
    font-weight: 400;
    font-size: 52px; line-height: 86px; letter-spacing: 1px;
    text-align: center; text-transform: uppercase;
    color: var(--headline-dark);
    -webkit-text-stroke: 2px var(--headline-dark);
  }
  .banner--sunset .banner__headline {
    color: var(--headline-light);
    -webkit-text-stroke: 2px var(--headline-light);
    text-shadow: 1px 2px 3px rgba(0,0,0,.35);
  }
</style>
</head>
<body>
<main class="canvas">

  <section class="banner banner--classic">
    <div class="banner__money" role="img" aria-label="Background collage of scattered dollar bills"></div>
    <div class="banner__frame">
      <div class="banner__photo" role="img" aria-label="Renovated lodge suite with a spiral staircase, green patterned curtains and a quilted bed"></div>
    </div>
    <h1 class="banner__headline">Check out our Million<br>Dollar Renovation!</h1>
  </section>

  <section class="banner banner--bright">
    <div class="banner__money" role="img" aria-label="Background collage of scattered dollar bills"></div>
    <div class="banner__frame">
      <div class="banner__photo" role="img" aria-label="Renovated lodge suite with a spiral staircase, green patterned curtains and a quilted bed"></div>
    </div>
    <h2 class="banner__headline">Check out our Million<br>Dollar Renovation!</h2>
  </section>

  <section class="banner banner--sunset">
    <div class="banner__money" role="img" aria-label="Background collage of scattered dollar bills"></div>
    <div class="banner__frame">
      <div class="banner__photo" role="img" aria-label="Renovated lodge suite with a spiral staircase, curtains and a quilted bed"></div>
    </div>
    <div class="banner__tint"></div>
    <h2 class="banner__headline">Check out our Million<br>Dollar Renovation!</h2>
  </section>

</main>
</body>
</html>
```